New Bicycle shop business card

Hi!
I'm looking for a business card for my new proffesional bike mechanics shop. This shop is only for fixing broken bikes and not selling bikes.
Peferbly a modern and sleek and modern design.
Colors: black, grey, red, white
Information:
Name: Rijwielwerkplaats Vanhoutte
Shop owner: Bart Vanhoutte & Marieke Segers
Website: www.rijwielwerkplaats-vanhoutte.be
Email: info@rijwielwerkplaats-vanhoutte.be
Phone number: +32471902368
Street adres: Kerkweg 46
9940 Bellebeke
Slogan/shop information: Herstellingen van alle merken.
Logo: see files.
Target Market(s)
People who seek a mechanic to fix or upgrade their bikes.
Contact Information for Business Card
Information:
Website: info@rijwielwerkplaats-vanhoutte.be
9940 Bellebeke
Logo: see files.

```html
<!DOCTYPE html>
<html lang="nl">
<head>
<meta charset="utf-8">
<title>Rijwielwerkplaats Vanhoutte – Business Card</title>
<link rel="stylesheet" href="https://fonts.googleapis.com/css2?family=Open+Sans:wght@400;600;700&display=swap">
<style>
  :root {
    --bg: #6b6b6b;
    --card-white: #ffffff;
    --card-black: #0b0b0c;
    --red: #e8222f;
    --ink: #1b1b1b;
    --grey-text: #4a4a4a;
    --faint: #f7e6e7;
    --white: #ffffff;
  }
  * { box-sizing: border-box; margin: 0; padding: 0; }
  html, body { width: 1200px; height: 1200px; overflow: hidden; }
  body {
    background: var(--bg);
    font-family: "Open Sans", Arial, sans-serif;
    position: relative;
  }
  .card {
    position: absolute;
    left: 240px;
    width: 720px;
    height: 418px;
    border-radius: 29px;
    overflow: hidden;
  }

  /* Front */
  .card-front { top: 142px; background: var(--card-white); }
  .front-decor {
    position: absolute; right: -90px; top: 160px;
    width: 270px; height: 270px; border-radius: 50%;
    background: var(--faint);
  }
  .brand {
    position: absolute; left: 28px; top: 78px;
    display: flex; align-items: center; gap: 10px;
  }
  .brand-square { width: 18px; height: 18px; background: var(--red); }
  .brand-name { font-weight: 700; font-size: 19px; color: var(--ink); }

  .owners { position: absolute; right: 38px; top: 72px; text-align: right; }
  .owners-label { color: var(--red); font-size: 18px; font-weight: 600; line-height: 24px; }
  .owners-names { color: var(--ink); font-size: 19px; font-weight: 700; line-height: 26px; }
  .owners-bar { position: absolute; right: 0; top: 72px; width: 8px; height: 52px; background: var(--red); }

  .details { position: absolute; left: 28px; top: 193px; }
  .company { color: var(--red); font-size: 20px; font-weight: 700; line-height: 26px; }
  .role { color: var(--ink); font-size: 15px; font-weight: 600; line-height: 22px; }
  .rule { width: 20px; height: 2px; background: var(--red); margin: 6px 0 8px; }
  .address { color: var(--grey-text); font-size: 18px; line-height: 22px; }
  .contact-list { list-style: none; margin-top: 8px; }
  .contact-list li {
    display: flex; align-items: center; gap: 11px;
    color: var(--grey-text); font-size: 17px; line-height: 30px;
  }
  .icon { width: 16px; height: 16px; flex: none; }

  .front-band { position: absolute; left: 0; bottom: 0; width: 100%; height: 13px; background: var(--red); }

  /* Back */
  .card-back { top: 638px; height: 420px; background: var(--card-black); }
  .back-pattern { position: absolute; inset: 0; background: #0e0e0f; }
  .back-brand {
    position: absolute; left: 0; right: 0; top: 150px;
    display: flex; flex-direction: column; align-items: center; gap: 22px;
  }
  .back-brand .brand-square { width: 26px; height: 26px; }
  .back-brand-name { color: var(--white); font-size: 32px; font-weight: 700; }
  .tagline {
    position: absolute; left: 0; right: 0; top: 362px;
    text-align: center; color: var(--white); font-size: 15px; font-weight: 600;
  }
</style>
</head>
<body>
  <section class="card card-front">
    <div class="front-decor" aria-hidden="true"></div>

    <div class="brand">
      <span class="brand-square"></span>
      <span class="brand-name">Rijwielwerkplaats Vanhoutte</span>
    </div>

    <div class="owners">
      <p class="owners-label">Shop owner:</p>
      <p class="owners-names">Bart Vanhoutte &amp; Marieke Segers</p>
    </div>
    <div class="owners-bar"></div>

    <div class="details">
      <p class="company">Rijwielwerkplaats Vanhoutte</p>
      <p class="role">General Manager</p>
      <div class="rule"></div>
      <p class="address">Kerkweg 46<br>9940 Bellebeke</p>
      <ul class="contact-list">
        <li>
          <svg class="icon" viewBox="0 0 16 16" aria-hidden="true">
            <rect width="16" height="16" fill="#e8222f"/>
            <path d="M5 3.5l1.6 2-1 1a6 6 0 0 0 3.9 3.9l1-1 2 1.6-1 1.5C8 12.5 3.5 8 3.5 4.5z" fill="#fff"/>
          </svg>
          +32471902368
        </li>
        <li>
          <svg class="icon" viewBox="0 0 16 16" aria-hidden="true">
            <rect width="16" height="16" fill="#e8222f"/>
            <rect x="3.5" y="5" width="9" height="6.5" fill="#fff"/>
            <path d="M3.5 5l4.5 3.5L12.5 5" stroke="#e8222f" stroke-width="1" fill="none"/>
          </svg>
          info@rijwielwerkplaats-vanhoutte.be
        </li>
        <li>
          <svg class="icon" viewBox="0 0 16 16" aria-hidden="true">
            <rect width="16" height="16" fill="#e8222f"/>
            <circle cx="8" cy="8" r="4.5" fill="none" stroke="#fff" stroke-width="1.3"/>
            <path d="M3.5 8h9M8 3.5c-2 2.5-2 6.5 0 9M8 3.5c2 2.5 2 6.5 0 9" stroke="#fff" stroke-width="1" fill="none"/>
          </svg>
          www.rijwielwerkplaats-vanhoutte.be
        </li>
      </ul>
    </div>

    <div class="front-band"></div>
  </section>

  <section class="card card-back">
    <div class="back-pattern" role="img" aria-label="Subtle repeating brand pattern in dark grey"></div>
    <div class="back-brand">
      <span class="brand-square"></span>
      <span class="back-brand-name">Rijwielwerkplaats Vanhoutte</span>
    </div>
    <p class="tagline">Herstellingen van alle merken.</p>
  </section>
</body>
</html>
```